Bench Advertisement - We Buy Houses Design Needed

Need a catchy, simple but elegant design for bus benches to advertise our company.

We need our website, or phone number, and a smal description (1-2 bulletpoints of what we do and what we offer)

The tricky part is for the designer to fit everything and make the website name as part of the title and fitting everything so that people passing by on the street can see what we offer.

Our website is quickdealhomebuyer.com - (916) 555-0143

Something simple but something that catches the eye of walking pedestrians, and drivers driving by the bench.

Our company buys houses, any condition, any situation, we buy houses for cash and close quickly. You can use this description to create a few bulletpoints however you like. Must follow dimensions in attachment.

Target Market(s)

People in foreclosure, about to lose their homes, people that need a quick cash sale of their property

Industry/Entity Type

Real Estate

Requirements
Must have
• catchy, website name, phone number, few brief bulletpoints about what we offer, colors that will catch peoples eye while walking or driving - advertisement will be placed on bus benches - visit our website to see the type of houses we buy - Also have more work for winner of design with possible bonuses
Nice to have
• Feel free to use description or images on our website - make sure the description is just bullet points and it fits with the overall theme / size of the advertisement - Bold bright colors - put yourself in their shoes (if you were going through financial difficulties and about to lose your house to foreclosure or auction, what would you want to see to pick up the phone and call us for a quick sale of your house?) (or if you have a house that you are having a problem with, problem renters, unkept/beat up house, what would make you want to call us and sell your house to us?)

```html
<!DOCTYPE html>
<html lang="en">
<head>
<meta charset="utf-8">
<title>Quick Deal Home Buyer – Bench Ad</title>
<link rel="stylesheet" href="https://fonts.googleapis.com/css2?family=Oswald:wght@300;400&display=swap">
<style>
  :root {
    --page-bg: #e9ede4;
    --band-dark: #3f6a2d;
    --band-mid: #6f9b32;
    --photo-light: #c9d64a;
    --photo-mid: #8fae3c;
    --photo-deep: #5d8a2e;
    --text-light: #f4f8ea;
    --text-dark: #355a22;
  }
  * { margin: 0; padding: 0; box-sizing: border-box; }
  html, body {
    width: 1200px; height: 1061px; overflow: hidden;
    background: var(--page-bg);
    font-family: "Oswald", "Arial Narrow", sans-serif;
  }
  .bench-ad {
    position: absolute; left: 40px; top: 250px;
    width: 1120px; height: 560px;
    background: var(--band-dark);
    box-shadow: 0 8px 24px rgba(0,0,0,.18);
  }
  .info-band {
    position: absolute; left: 0; top: 95px;
    width: 100%; height: 305px;
    background: var(--band-mid);
  }
  .photo-area {
    position: absolute; left: 0; top: 0;
    width: 460px; height: 100%;
    background: radial-gradient(ellipse at 40% 20%, var(--photo-light), var(--photo-mid) 55%, var(--photo-deep) 100%);
    -webkit-mask-image: linear-gradient(to right, #000 80%, transparent);
            mask-image: linear-gradient(to right, #000 80%, transparent);
  }
  .brand {
    position: absolute; left: 28px; top: 70px;
    display: flex; align-items: center; gap: 8px;
    color: var(--text-light);
    font-weight: 300; font-size: 15px; letter-spacing: .5px;
    text-transform: uppercase;
  }
  .brand-mark { width: 12px; height: 12px; background: var(--text-dark); }
  .photo-caption {
    position: absolute; left: 60px; bottom: 14px;
    color: var(--text-light); font-weight: 300; font-size: 15px;
  }
  .offer {
    position: absolute; left: 470px; right: 20px; top: 18px;
    text-align: center; color: var(--text-light);
  }
  .website { font-weight: 400; font-size: 54px; line-height: 1.1; }
  .phone {
    display: flex; justify-content: center; align-items: center; gap: 14px;
    color: var(--text-dark); font-size: 46px; font-weight: 300; margin-top: 6px;
  }
  .phone svg { width: 40px; height: 40px; }
  .points { list-style: none; margin-top: 16px; font-weight: 300; font-size: 27px; line-height: 1.5; }
  .points li { display: flex; justify-content: center; align-items: center; gap: 10px; }
  .marker { width: 0; height: 0; border-top: 9px solid transparent; border-bottom: 9px solid transparent; }
  .marker-right { border-left: 9px solid #2f4f1c; }
  .marker-left { border-right: 9px solid #2f4f1c; }
</style>
</head>
<body>
  <div class="bench-ad">
    <div class="info-band">
      <div class="photo-area" role="img" aria-label="Photo of one hand handing over a paper house while another hand holds a dollar bill, on a blurred green background"></div>
      <div class="brand"><span class="brand-mark"></span>Quick Deal Home Buyer</div>
      <p class="photo-caption">pick up the phone and call us for a quick sale of your house</p>
      <div class="offer">
        <div class="website">quickdealhomebuyer.com</div>
        <div class="phone">
          <svg viewBox="0 0 40 40" aria-hidden="true">
            <circle cx="20" cy="20" r="17" fill="none" stroke="currentColor" stroke-width="2.5"/>
            <path d="M14 11c1.5-1 3-.5 3.5 1l1 3c.3 1-.3 1.8-1.2 2.3 1 2.5 2.8 4.3 5.2 5.3.5-.9 1.3-1.5 2.3-1.2l3 1c1.5.5 2 2 1 3.5-1.5 2-4 2.5-6.5 1.3-4.5-2.2-7.8-5.6-9.8-10-1-2.5-.5-5 1.5-6.2z" fill="currentColor"/>
          </svg>
          <span>(916) 555-0143</span>
        </div>
        <ul class="points">
          <li>Our company buys houses, Any condition, Any situation</li>
          <li><span class="marker marker-right"></span>We buy houses for cash and close quickly<span class="marker marker-left"></span></li>
        </ul>
      </div>
    </div>
  </div>
</body>
</html>
```